Mastering Modern Vineyard Management

size of the ad - 8”x 10.75" plus 0.25" bleed
I would like an ad for a magazine that will stand out and make people want to read the ad.
The ad should not be crowded and people reading the ad will be able to read the text.
I would like it to be a creative and modern-day design.
the list of topics should not be the focus of the ad.
the text is attached.
If you decide to use people in the ad then please no ladies.
please note that leave over 1 inch for the bottom of the footer

```html
<!DOCTYPE html>
<html lang="en">
<head>
<meta charset="utf-8">
<title>Vineyard Course – Mastering Modern Vineyard Management</title>
<link rel="stylesheet" href="https://fonts.googleapis.com/css2?family=Libre+Baskerville:wght@400;700&family=Overpass:wght@400;600;700;800&display=swap">
<style>
  :root {
    --navy: #0f3960;
    --band-blue: #0d4a87;
    --bright-blue: #1b6fbd;
    --yellow: #f7ee2c;
    --light-grey: #ebebeb;
    --ink: #1c1c1c;
    --tick-orange: #e8532a;
    --white: #ffffff;
    --divider: #b9b9b9;
  }
  * { box-sizing: border-box; margin: 0; padding: 0; }
  html, body { width: 935px; height: 1200px; overflow: hidden; background: #f2f2f2; }
  .ad {
    position: relative; width: 935px; height: 1200px; overflow: hidden;
    font-family: "Overpass", "Helvetica Neue", Arial, sans-serif; color: var(--ink);
  }

  /* Hero */
  .hero { position: absolute; left: 0; top: 0; width: 935px; height: 675px; background: var(--navy); }
  .hero-title {
    position: absolute; top: 52px; width: 100%; text-align: center;
    font-family: "Libre Baskerville", Georgia, serif; font-weight: 700;
    font-size: 59px; line-height: 72px; color: #efefef; letter-spacing: -0.5px;
  }
  .hero-subtitle {
    position: absolute; top: 136px; width: 100%; text-align: center;
    font-family: "Libre Baskerville", Georgia, serif; font-weight: 400;
    font-size: 33px; line-height: 43px; color: var(--yellow);
  }
  .scene { position: absolute; left: 0; top: 240px; width: 935px; height: 435px; }

  /* Tagline */
  .tagline {
    position: absolute; top: 675px; left: 0; width: 935px; height: 66px; background: var(--light-grey);
    display: flex; align-items: center; justify-content: center;
    font-weight: 800; font-size: 33px; color: var(--bright-blue); letter-spacing: -0.2px;
  }

  /* Course details band */
  .details { position: absolute; top: 741px; left: 0; width: 935px; height: 112px; background: var(--band-blue); color: var(--white); }
  .details-col { position: absolute; top: 0; height: 112px; display: flex; flex-direction: column; justify-content: center; text-align: center; }
  .details-col.location { left: 40px; width: 320px; }
  .details-col.schedule { left: 381px; width: 292px; }
  .details-col.start { left: 688px; width: 220px; }
  .details-divider { position: absolute; top: 22px; width: 2px; height: 68px; background: #b7c6d8; }
  .details-main { font-size: 30px; font-weight: 400; line-height: 34px; }
  .details-accent { color: var(--yellow); font-weight: 800; font-size: 28px; line-height: 32px; }
  .details-note { color: var(--yellow); font-weight: 600; font-size: 15px; margin-top: 2px; }

  /* Offer and topics */
  .offer { position: absolute; top: 853px; left: 0; width: 935px; height: 220px; background: var(--light-grey); }
  .perks { position: absolute; left: 58px; top: 44px; list-style: none; }
  .perk { display: flex; gap: 24px; font-size: 19px; font-weight: 600; line-height: 25px; margin-bottom: 15px; }
  .perk svg { flex: none; width: 20px; height: 20px; margin-top: 1px; }
  .offer-divider { position: absolute; left: 456px; top: 35px; width: 2px; height: 150px; background: var(--divider); }
  .topics-heading { position: absolute; left: 494px; top: 32px; font-size: 22px; line-height: 26px; font-weight: 800; color: var(--bright-blue); }
  .topics { position: absolute; top: 63px; list-style: none; font-size: 15px; line-height: 26.3px; }
  .topics.first { left: 496px; }
  .topics.second { left: 740px; }
  .topics li { display: flex; align-items: center; gap: 7px; }
  .topics svg { width: 10px; height: 10px; flex: none; }

  /* Footer */
  .footer { position: absolute; top: 1073px; left: 0; width: 935px; height: 127px; background: var(--white); }
  .org { position: absolute; left: 58px; top: 27px; }
  .org-name { font-size: 17px; font-weight: 800; color: var(--bright-blue); line-height: 20px; }
  .org-tag { font-size: 10px; font-weight: 700; color: var(--bright-blue); margin-top: 5px; }
  .contact { position: absolute; left: 334px; top: 18px; font-size: 12.5px; line-height: 19px; }
  .contact-row { display: flex; align-items: center; gap: 6px; }
  .contact-row svg { width: 12px; height: 12px; flex: none; }
  .contact-row .gap { margin-left: 12px; }
  .sponsor { font-size: 10px; color: #333; margin-top: 1px; }
  .partner { position: absolute; left: 654px; top: 24px; width: 225px; }
  .partner-name { display: flex; align-items: center; gap: 9px; font-size: 19px; line-height: 21px; font-weight: 700; color: var(--band-blue); }
  .partner-name .mark { flex: none; width: 30px; height: 30px; background: var(--band-blue); }
  .partner-tag { font-size: 9.5px; color: var(--band-blue); margin-top: 7px; }
</style>
</head>
<body>
<div class="ad">
  <section class="hero">
    <h1 class="hero-title">VINEYARD COURSE</h1>
    <p class="hero-subtitle">MASTERING MODERN VINEYARD<br>MANAGEMENT</p>
    <svg class="scene" role="img" aria-label="Rows of grapevines across rolling vineyard hills" viewBox="0 0 935 435" preserveAspectRatio="none">
      <defs>
        <linearGradient id="scene-fill" x1="0" y1="0" x2="0" y2="1">
          <stop offset="0" stop-color="#0f3960"/>
          <stop offset="0.35" stop-color="#7f9fba"/>
          <stop offset="0.7" stop-color="#dfe6ec"/>
          <stop offset="1" stop-color="#bfdcec"/>
        </linearGradient>
      </defs>
      <rect width="935" height="435" fill="url(#scene-fill)"/>
    </svg>
  </section>

  <div class="tagline">Investing in knowledge is investing in opportunities</div>

  <section class="details">
    <div class="details-col location">
      <div class="details-main">Location: BROOKVALE</div>
      <div class="details-note">Remote: for out of BROOKVALE Area</div>
    </div>
    <div class="details-divider" style="left:374px"></div>
    <div class="details-col schedule">
      <div class="details-main">10 WEDNESDAY</div>
      <div class="details-accent">7:30 PM –9:30 PM</div>
    </div>
    <div class="details-divider" style="left:680px"></div>
    <div class="details-col start">
      <div class="details-main">STARTING</div>
      <div class="details-accent">MARCH 8</div>
    </div>
  </section>

  <section class="offer">
    <ul class="perks">
      <li class="perk"><svg viewBox="0 0 20 20"><rect x="1.5" y="3.5" width="15" height="15" fill="none" stroke="#e8532a" stroke-width="2"/><path d="M5 10 l4 4 l9 -11" fill="none" stroke="#e8532a" stroke-width="2.6"/></svg>Limited Partial Scholarships</li>
      <li class="perk"><svg viewBox="0 0 20 20"><rect x="1.5" y="3.5" width="15" height="15" fill="none" stroke="#e8532a" stroke-width="2"/><path d="M5 10 l4 4 l9 -11" fill="none" stroke="#e8532a" stroke-width="2.6"/></svg>Early Bird Special</li>
      <li class="perk"><svg viewBox="0 0 20 20"><rect x="1.5" y="3.5" width="15" height="15" fill="none" stroke="#e8532a" stroke-width="2"/><path d="M5 10 l4 4 l9 -11" fill="none" stroke="#e8532a" stroke-width="2.6"/></svg><span>For those that started or<br>would like to go into viticulture</span></li>
    </ul>
    <div class="offer-divider"></div>
    <h2 class="topics-heading">TOPICS: PARTIAL LISTING</h2>
    <ul class="topics first">
      <li><svg viewBox="0 0 10 10"><circle cx="5" cy="5" r="5" fill="#1b6fbd"/><path d="M2.6 5.1 l1.6 1.6 l3.2 -3.3" fill="none" stroke="#fff" stroke-width="1.3"/></svg>Canopy management</li>
      <li><svg viewBox="0 0 10 10"><circle cx="5" cy="5" r="5" fill="#1b6fbd"/><path d="M2.6 5.1 l1.6 1.6 l3.2 -3.3" fill="none" stroke="#fff" stroke-width="1.3"/></svg>Soil and nutrition</li>
      <li><svg viewBox="0 0 10 10"><circle cx="5" cy="5" r="5" fill="#1b6fbd"/><path d="M2.6 5.1 l1.6 1.6 l3.2 -3.3" fill="none" stroke="#fff" stroke-width="1.3"/></svg>Pest and disease control</li>
      <li><svg viewBox="0 0 10 10"><circle cx="5" cy="5" r="5" fill="#1b6fbd"/><path d="M2.6 5.1 l1.6 1.6 l3.2 -3.3" fill="none" stroke="#fff" stroke-width="1.3"/></svg>Irrigation planning</li>
      <li><svg viewBox="0 0 10 10"><circle cx="5" cy="5" r="5" fill="#1b6fbd"/><path d="M2.6 5.1 l1.6 1.6 l3.2 -3.3" fill="none" stroke="#fff" stroke-width="1.3"/></svg>Harvest timing</li>
    </ul>
    <ul class="topics second">
      <li><svg viewBox="0 0 10 10"><circle cx="5" cy="5" r="5" fill="#1b6fbd"/><path d="M2.6 5.1 l1.6 1.6 l3.2 -3.3" fill="none" stroke="#fff" stroke-width="1.3"/></svg>Pruning</li>
      <li><svg viewBox="0 0 10 10"><circle cx="5" cy="5" r="5" fill="#1b6fbd"/><path d="M2.6 5.1 l1.6 1.6 l3.2 -3.3" fill="none" stroke="#fff" stroke-width="1.3"/></svg>Trellis systems</li>
      <li><svg viewBox="0 0 10 10"><circle cx="5" cy="5" r="5" fill="#1b6fbd"/><path d="M2.6 5.1 l1.6 1.6 l3.2 -3.3" fill="none" stroke="#fff" stroke-width="1.3"/></svg>Vine budgeting</li>
      <li><svg viewBox="0 0 10 10"><circle cx="5" cy="5" r="5" fill="#1b6fbd"/><path d="M2.6 5.1 l1.6 1.6 l3.2 -3.3" fill="none" stroke="#fff" stroke-width="1.3"/></svg>Grape sourcing</li>
      <li><svg viewBox="0 0 10 10"><circle cx="5" cy="5" r="5" fill="#1b6fbd"/><path d="M2.6 5.1 l1.6 1.6 l3.2 -3.3" fill="none" stroke="#fff" stroke-width="1.3"/></svg>Certification</li>
    </ul>
  </section>

  <footer class="footer">
    <div class="org">
      <div class="org-name">CRESTLINE<br>CAREER SERVICE</div>
      <div class="org-tag">A NON-PROFIT OF HARBOR LEAGUE</div>
    </div>
    <div class="contact">
      <div class="contact-row"><svg viewBox="0 0 12 12"><circle cx="6" cy="6" r="5.3" fill="none" stroke="#1b6fbd"/><path d="M6 9 C4 6.5 3.8 5.6 3.8 4.9 a2.2 2.2 0 0 1 4.4 0 C8.2 5.6 8 6.5 6 9z" fill="#1b6fbd"/></svg>Brookvale- out of Brookvale Area</div>
      <div class="contact-row"><svg viewBox="0 0 12 12"><circle cx="6" cy="6" r="5.3" fill="none" stroke="#1b6fbd"/><path d="M4 3.3 l1.2 1.6 l-0.7 0.8 q0.7 1.4 2 2 l0.8 -0.7 l1.6 1.2 l-0.8 1 q-3.8 -0.6 -5 -4.9z" fill="#1b6fbd"/></svg>555 014 2290 x 210</div>
      <div class="contact-row"><svg viewBox="0 0 12 12"><circle cx="6" cy="6" r="5.3" fill="none" stroke="#1b6fbd"/><rect x="3.3" y="4.2" width="5.4" height="3.8" fill="#1b6fbd"/><path d="M3.3 4.2 l2.7 2 l2.7 -2" fill="none" stroke="#fff" stroke-width="0.6"/></svg>info@crestline.org
        <svg class="gap" viewBox="0 0 12 12"><circle cx="6" cy="6" r="5.3" fill="none" stroke="#1b6fbd"/><circle cx="6" cy="6" r="3" fill="none" stroke="#1b6fbd" stroke-width="0.8"/><path d="M3 6 h6 M6 3 v6" stroke="#1b6fbd" stroke-width="0.7"/></svg>www.crestline.org</div>
      <div class="sponsor">Sponsored in part by the Marlow family foundation</div>
    </div>
    <div class="partner">
      <div class="partner-name"><span class="mark"></span><span>ALDER<br>TITLE AGENCY</span></div>
      <div class="partner-tag">An Alder Commercial Services Company</div>
    </div>
  </footer>
</div>
</body>
</html>
```